Corvane Capital Business Cards

These are professional business cards that are for my family office.
Put fake emails and phone numbers as of now until I finalize those components. This family office controls my families investments, assets, and future. The cards should be professional.
..
.
.
.
I just uploaded another variation of a logo I would like to see as a business card to I am inbeteen which logo to use

Target Market(s)

business

Industry/Entity Type

business

Contact Information for Business Card

Professional, wealth related, finance related.

Requirements
Must have
• Logo

```html
<!DOCTYPE html>
<html lang="en">
<head>
<meta charset="utf-8">
<title>Corvane Capital Business Cards</title>
<link rel="stylesheet" href="https://fonts.googleapis.com/css2?family=Playfair+Display:wght@400&family=Tinos:wght@400;700&display=swap">
<style>
  :root {
    --bg: #e4e4e2;
    --card: #ffffff;
    --ink: #111111;
    --gold: #c4ac6e;
    --shadow: rgba(0, 0, 0, 0.18);
  }
  * { box-sizing: border-box; margin: 0; padding: 0; }
  html, body {
    width: 1200px;
    height: 900px;
    overflow: hidden;
    background: var(--bg);
  }
  .canvas {
    position: relative;
    width: 1200px;
    height: 900px;
  }
  .card {
    position: absolute;
    width: 560px;
    height: 320px;
    background: var(--card);
    box-shadow: 0 10px 28px var(--shadow);
    overflow: hidden;
  }
  .card--front { left: 60px; top: 100px; }
  .card--back { left: 580px; top: 480px; }

  .wordmark {
    font-family: "Playfair Display", serif;
    font-weight: 400;
    color: var(--ink);
    text-transform: uppercase;
    letter-spacing: 0.06em;
    display: flex;
    align-items: center;
    white-space: nowrap;
  }
  .wordmark__square {
    display: inline-block;
    background: var(--gold);
  }
  .card--front .wordmark {
    position: absolute;
    left: 0; right: 0; top: 0; bottom: 0;
    justify-content: center;
    font-size: 40px;
    gap: 18px;
  }
  .card--front .wordmark__square { width: 22px; height: 22px; }

  .card--back .wordmark {
    position: absolute;
    right: 36px;
    top: 58px;
    font-size: 24px;
    gap: 12px;
  }
  .card--back .wordmark__square { width: 14px; height: 14px; }

  .rule {
    position: absolute;
    left: 190px;
    right: 30px;
    top: 180px;
    height: 2px;
    background: var(--gold);
  }
  .person {
    position: absolute;
    left: 36px;
    top: 158px;
    font-family: "Tinos", serif;
  }
  .person__name {
    font-size: 24px;
    font-weight: 700;
    color: var(--ink);
    line-height: 1;
  }
  .person__name .surname { color: var(--gold); }
  .person__role {
    font-size: 16px;
    color: var(--ink);
    margin-top: 4px;
  }
  .contact {
    position: absolute;
    left: 58px;
    top: 220px;
    list-style: none;
    font-family: "Tinos", serif;
    font-size: 16px;
    color: var(--ink);
  }
  .contact__item {
    display: flex;
    align-items: center;
    gap: 8px;
    line-height: 1.35;
  }
  .contact__icon { width: 14px; height: 14px; fill: var(--gold); }
  .bands {
    position: absolute;
    left: 0; top: 0;
    width: 560px; height: 320px;
  }
  .band--gold { fill: var(--gold); }
  .band--black { fill: var(--ink); }
</style>
</head>
<body>
<main class="canvas">

  <section class="card card--front" aria-label="Card front">
    <div class="wordmark"><span class="wordmark__square"></span>Corvane Capital</div>
  </section>

  <section class="card card--back" aria-label="Card back">
    <svg class="bands" viewBox="0 0 560 320" aria-hidden="true">
      <polygon class="band--gold" points="0,304 346,276 338,320 0,320"/>
      <polygon class="band--black" points="354,270 560,270 560,320 346,320"/>
    </svg>
    <div class="wordmark"><span class="wordmark__square"></span>Corvane Capital</div>
    <div class="rule"></div>
    <div class="person">
      <p class="person__name">Elias <span class="surname">Brandt</span></p>
      <p class="person__role">Founder</p>
    </div>
    <ul class="contact">
      <li class="contact__item">
        <svg class="contact__icon" viewBox="0 0 16 16" aria-hidden="true"><path d="M3.2 1.5l2.4 2.6-1.3 1.8c.9 2 2.4 3.5 4.4 4.4l1.8-1.3 2.6 2.4-1.6 2.6C6.4 13.6 2.4 9.6 1 4.5z"/></svg>
        555-014-2290
      </li>
      <li class="contact__item">
        <svg class="contact__icon" viewBox="0 0 16 16" aria-hidden="true"><path d="M1 3h14v10H1z M1.5 3.5L8 9l6.5-5.5" stroke="#fff" stroke-width="1"/></svg>
        info@corvanecapital.com
      </li>
    </ul>
  </section>

</main>
</body>
</html>
```